Redesign of business card for Cedar Ridge Mechanical

We are looking for a new design for our business cards for Cedar Ridge Mechanical. We are a plumbing & HVAC construction company, operating on the West Coast of Canada and USA. Logo attached.
Industry/Entity Type
Construction - Plumbing & HVAC
Contact Information for Business Card
Name, address, phone numbers, email, website address
Look and feel
Each slider illustrates characteristics of the customer's brand and the style your logo design should communicate.

```html
<!DOCTYPE html>
<html lang="en">
<head>
<meta charset="utf-8">
<title>Cedar Ridge Mechanical – Business Card</title>
<link href="https://fonts.googleapis.com/css2?family=Montserrat:wght@400;500;700&display=swap" rel="stylesheet">
<style>
  :root {
    --stage: #2a2a2a;
    --card: #171717;
    --card-edge: #222;
    --white: #ffffff;
    --grey: #8c8c8c;
    --grey-band: #a9a9a9;
    --faint: #2b2b2b;
  }
  * { margin: 0; padding: 0; box-sizing: border-box; }
  html, body {
    width: 1200px; height: 963px; overflow: hidden;
    background: var(--stage);
    font-family: "Montserrat", sans-serif;
  }
  .sheet {
    width: 1200px; height: 963px;
    display: flex; flex-direction: column; align-items: center; justify-content: center;
    gap: 60px;
  }
  .card {
    position: relative;
    width: 640px; height: 366px;
    background: var(--card);
    border-radius: 22px;
    border: 1px solid var(--card-edge);
    overflow: hidden;
    box-shadow: 0 14px 30px rgba(0,0,0,.45);
  }
  /* Front */
  .name-band {
    position: absolute; left: 0; top: 34px;
    width: 440px; height: 64px;
    background: var(--white);
    padding: 12px 0 0 46px;
  }
  .name {
    font-weight: 700; font-size: 22px; letter-spacing: .5px;
    color: var(--card); line-height: 1;
  }
  .name .surname { color: var(--grey); }
  .role {
    font-weight: 400; font-size: 14px; color: var(--grey); margin-top: 4px;
  }
  .side-strip {
    position: absolute; right: 0; top: 128px;
    width: 26px; height: 40px; background: var(--grey-band);
  }
  .brand {
    position: absolute; left: 452px; top: 34px;
    width: 160px; height: 134px;
    display: flex; flex-direction: column; align-items: center; justify-content: center;
    gap: 10px;
  }
  .brand-mark {
    width: 46px; height: 46px; border: 3px solid var(--white); border-radius: 6px;
  }
  .brand-name {
    font-weight: 700; font-size: 15px; color: var(--white);
    text-transform: uppercase; text-align: center; line-height: 1.2; letter-spacing: .5px;
  }
  .contact {
    position: absolute; left: 40px; top: 170px;
    list-style: none;
  }
  .contact li {
    display: flex; align-items: center; gap: 8px;
    font-size: 15px; color: var(--white); line-height: 1.55;
  }
  .contact svg { width: 13px; height: 13px; fill: var(--white); flex: none; }
  .address {
    position: absolute; right: 44px; bottom: 36px;
    text-align: right; font-size: 16px; color: var(--white); line-height: 1.3;
  }
  /* Back */
  .back {
    display: flex; flex-direction: column; align-items: center; justify-content: center; gap: 18px;
  }
  .back .brand-mark { width: 90px; height: 90px; border: 6px solid var(--faint); border-radius: 12px; }
  .back .brand-name { font-size: 30px; color: var(--faint); }
</style>
</head>
<body>
<main class="sheet">
  <section class="card front" aria-label="Business card front">
    <div class="name-band">
      <p class="name">DANIEL <span class="surname">BROOKS</span></p>
      <p class="role">Manager</p>
    </div>
    <div class="brand">
      <span class="brand-mark"></span>
      <p class="brand-name">Cedar Ridge Mechanical</p>
    </div>
    <div class="side-strip"></div>
    <ul class="contact">
      <li><svg viewBox="0 0 24 24"><path d="M6.6 10.8a15 15 0 0 0 6.6 6.6l2.2-2.2c.3-.3.7-.4 1-.2 1.1.4 2.3.6 3.6.6.6 0 1 .4 1 1V20c0 .6-.4 1-1 1A17 17 0 0 1 3 4c0-.6.4-1 1-1h3.5c.6 0 1 .4 1 1 0 1.3.2 2.5.6 3.6.1.3 0 .7-.2 1z"/></svg>123-456-2100</li>
      <li><svg viewBox="0 0 24 24"><path d="M2 5h20v14H2z M4 7v.5l8 5 8-5V7l-8 5z" fill-rule="evenodd"/></svg>youremail@mailbox.com</li>
      <li><svg viewBox="0 0 24 24"><circle cx="12" cy="12" r="10"/></svg>www.yourwebsite.com</li>
    </ul>
    <p class="address">Your address, city<br>state, ZIP 0000</p>
  </section>

  <section class="card back" aria-label="Business card back">
    <span class="brand-mark"></span>
    <p class="brand-name">Cedar Ridge Mechanical</p>
  </section>
</main>
</body>
</html>
```